International sports company needs packaging design for color box

We need this box for our yoga mats which we will sell online. This mat is very high quality and 100% environmentally friendly. The yoga mat comes in a stylish yoga bag that will be in the box.

Yoga enthusiasts, athletes, gymnasts, actually all people who do sporting activities and value environmental friendliness will be the contact group

The logo should be visible in any case. The creator is free to choose whether to use only the complete logo or the complete logo with the emblem. In terms of style, it should be reminiscent of a packaging box from Corvane's Vextal. Be as timeless, modern and elegant as possible. If an environmentally friendly detail can be added, this would certainly be a plus. Color should be black / white / gray.

Target Market(s)

Germany

Requirements
Must have
• Size for the color box should be 13x13x61.5 cm.

```html
<!DOCTYPE html>
<html lang="en">
<head>
<meta charset="utf-8">
<title>Kavro Yoga Mat – Box Dieline</title>
<link rel="stylesheet" href="https://fonts.googleapis.com/css2?family=Montserrat:wght@300;600&display=swap">
<style>
  :root {
    --backdrop: #d6d6d6;
    --board: #ffffff;
    --ink: #111111;
    --cut-line: #9a9a9a;
    --fold-line: #c4c4c4;
  }
  html, body {
    margin: 0;
    padding: 0;
    width: 1200px;
    height: 784px;
    overflow: hidden;
    background: var(--backdrop);
  }
  .canvas {
    position: relative;
    width: 1200px;
    height: 784px;
    background: var(--backdrop);
  }
  .dieline {
    position: absolute;
    left: 47px;
    top: 46px;
    width: 1106px;
    height: 692px;
  }
  .board { fill: var(--board); stroke: var(--cut-line); stroke-width: 0.8; }
  .fold { stroke: var(--fold-line); stroke-width: 0.8; stroke-dasharray: 4 3; fill: none; }
  .brand-name {
    font-family: "Montserrat", sans-serif;
    font-weight: 600;
    font-size: 17px;
    letter-spacing: 2px;
    fill: var(--ink);
  }
  .feature-list {
    font-family: "Montserrat", sans-serif;
    font-weight: 600;
    font-size: 9.5px;
    letter-spacing: 1.4px;
    fill: var(--ink);
  }
  .product-title {
    font-family: "Montserrat", sans-serif;
    font-weight: 300;
    font-size: 50px;
    letter-spacing: 7px;
    fill: var(--ink);
  }
  .title-frame { fill: none; stroke: var(--ink); stroke-width: 2; }
  .eco-badge { fill: none; stroke: var(--ink); stroke-width: 1.2; }
  .end-seal { fill: var(--ink); }
  .brand-dot { fill: var(--ink); }
</style>
</head>
<body>
<main class="canvas">
  <svg class="dieline" viewBox="57 78 1053 659" xmlns="http://www.w3.org/2000/svg" aria-label="Flat dieline of the yoga mat box">
    <!-- top closing panel with dust tabs -->
    <path class="board" d="M240 78 H925 L1008 88 Q1018 90 1018 100 V216 Q1018 226 1008 228 L925 236 H240 L157 228 Q147 226 147 216 V100 Q147 90 157 88 Z"/>
    <!-- front panel with end flaps -->
    <path class="board" d="M240 236 H925 H1085 L1110 248 V383 L1085 395 H925 H240 H82 L57 383 V248 L82 236 Z"/>
    <!-- back panel with dust tabs -->
    <path class="board" d="M240 395 H925 L1008 405 Q1018 407 1018 417 V533 Q1018 543 1008 545 L925 553 H240 L157 545 Q147 543 147 533 V417 Q147 407 157 405 Z"/>
    <!-- side panel and glue flap -->
    <path class="board" d="M240 553 H925 V711 L915 730 Q911 737 902 737 H263 Q254 737 250 730 L240 711 Z"/>

    <!-- fold lines -->
    <line class="fold" x1="240" y1="78" x2="240" y2="711"/>
    <line class="fold" x1="925" y1="78" x2="925" y2="711"/>
    <line class="fold" x1="82" y1="236" x2="1085" y2="236"/>
    <line class="fold" x1="82" y1="395" x2="1085" y2="395"/>
    <line class="fold" x1="147" y1="553" x2="1018" y2="553"/>
    <line class="fold" x1="240" y1="711" x2="925" y2="711"/>
    <line class="fold" x1="82" y1="236" x2="82" y2="395"/>
    <line class="fold" x1="1085" y1="236" x2="1085" y2="395"/>

    <!-- panel: brand and features (top) -->
    <g class="info-panel">
      <circle class="brand-dot" cx="318" cy="158" r="7"/>
      <text class="brand-name" x="334" y="164">KAVRO</text>
      <circle class="eco-badge" cx="563" cy="160" r="34" role="img" aria-label="Environmentally friendly badge"/>
      <text class="feature-list" x="662" y="142">HIGH QUALITY YOGA MAT</text>
      <text class="feature-list" x="662" y="164">100% ENVIRONMENTALLY FRIENDLY</text>
      <text class="feature-list" x="662" y="185">COMES IN STYLISH YOGA BAG</text>
    </g>

    <!-- panel: title (front) -->
    <g class="title-panel">
      <rect class="title-frame" x="286" y="259" width="596" height="112"/>
      <text class="product-title" x="590" y="333" text-anchor="middle">YOGA MAT</text>
    </g>

    <!-- end flap seal -->
    <circle class="end-seal" cx="162" cy="316" r="43" role="img" aria-label="Environmentally friendly end seal"/>

    <!-- panel: brand and features (back) -->
    <g class="info-panel">
      <circle class="brand-dot" cx="318" cy="476" r="7"/>
      <text class="brand-name" x="334" y="482">KAVRO</text>
      <circle class="eco-badge" cx="563" cy="476" r="34" role="img" aria-label="Environmentally friendly badge"/>
      <text class="feature-list" x="662" y="459">HIGH QUALITY YOGA MAT</text>
      <text class="feature-list" x="662" y="481">100% ENVIRONMENTALLY FRIENDLY</text>
      <text class="feature-list" x="662" y="503">COMES IN STYLISH YOGA BAG</text>
    </g>

    <!-- panel: title (side) -->
    <g class="title-panel">
      <rect class="title-frame" x="286" y="577" width="596" height="112"/>
      <text class="product-title" x="590" y="651" text-anchor="middle">YOGA MAT</text>
    </g>
  </svg>
</main>
</body>
</html>
```